Moravel Aesthetic Doctor

I require an elegant, luxurious looking business card for my aesthetic business. I am a doctor and that will set me aside from competitors. I am planning to provide home and spa based treatments to clients with high expectations. I have attached my logo.

```html
<!DOCTYPE html>
<html lang="en">
<head>
<meta charset="utf-8">
<title>Moravel Aesthetic Doctor – Business Card</title>
<link rel="stylesheet" href="https://fonts.googleapis.com/css2?family=Arimo:wght@400;700&display=swap">
<style>
  :root {
    --backdrop: #202022;
    --card: #0d0d0e;
    --card-edge: #1a1a1c;
    --ink: #e9e9ea;
    --ink-soft: #bdbdc0;
    --accent: #5ab8ec;
    --rule: #4a4a4e;
  }
  * { box-sizing: border-box; margin: 0; padding: 0; }
  html, body {
    width: 1200px; height: 900px; overflow: hidden;
    background: var(--backdrop);
    font-family: "Arimo", Arial, sans-serif;
  }
  .stage {
    width: 1200px; height: 900px;
    display: flex; align-items: center; justify-content: center; gap: 40px;
  }
  .card {
    position: relative;
    width: 540px; height: 310px;
    border-radius: 22px;
    background: radial-gradient(ellipse at 60% 30%, var(--card-edge), var(--card) 70%);
    box-shadow: 0 18px 40px rgba(0,0,0,.55);
    color: var(--ink);
  }
  .brand {
    position: absolute; left: 0; right: 0; top: 54px;
    display: flex; align-items: center; justify-content: center; gap: 16px;
  }
  .brand-mark {
    width: 64px; height: 64px; border-radius: 50%;
    border: 2px solid var(--ink-soft);
  }
  .brand-name {
    font-weight: 400; font-size: 22px; letter-spacing: 3px;
    text-transform: uppercase; line-height: 1.35;
    color: var(--ink);
  }
  .card-front .brand-name { color: var(--accent); }
  .divider {
    position: absolute; left: 60px; right: 60px; top: 150px;
    height: 1px;
    background: linear-gradient(90deg, transparent, var(--rule), transparent);
  }
  .person { position: absolute; left: 44px; top: 180px; }
  .person-name { font-size: 22px; font-weight: 700; color: var(--ink); }
  .person-name .credentials { font-weight: 400; font-size: 15px; color: var(--accent); margin-left: 4px; }
  .person-role { font-size: 15px; color: var(--accent); margin-top: 3px; }
  .person-rule { width: 300px; height: 1px; background: var(--rule); margin: 10px 0 8px; }
  .contact-list { list-style: none; font-size: 14px; color: var(--ink); }
  .contact-list li { display: flex; align-items: center; gap: 9px; line-height: 20px; }
  .contact-list svg { width: 13px; height: 13px; flex: none; }
  .social {
    position: absolute; left: 372px; top: 262px;
    display: flex; gap: 8px;
  }
  .social-dot { width: 22px; height: 22px; border-radius: 50%; border: 1.5px solid var(--accent); }
  .services {
    position: absolute; left: 0; right: 0; top: 176px;
    text-align: center; font-size: 14px; line-height: 21px; color: var(--ink);
  }
  .services .sep { display: inline-block; width: 5px; height: 5px; border-radius: 50%; background: var(--ink); vertical-align: middle; margin: 0 8px; }
  .card-back .divider { top: 152px; }
</style>
</head>
<body>
<main class="stage">
  <section class="card card-front" aria-label="Card front">
    <div class="brand">
      <span class="brand-mark"></span>
      <span class="brand-name">Moravel<br>Aesthetic Doctor</span>
    </div>
    <div class="divider"></div>
    <div class="person">
      <p class="person-name">Dr Elena Varga<span class="credentials">MRCPCH MD</span></p>
      <p class="person-role">Australasian Diploma of Aesthetic Medicine</p>
      <div class="person-rule"></div>
      <ul class="contact-list">
        <li><svg viewBox="0 0 16 16" aria-hidden="true"><path fill="#5ab8ec" d="M3 1l3 3-1.5 2a9 9 0 005.5 5.5L12 10l3 3-2 2C7 15 1 9 1 3z"/></svg>0800 555 014</li>
        <li><svg viewBox="0 0 16 16" aria-hidden="true"><rect x="1" y="3" width="14" height="10" fill="#5ab8ec"/><path d="M1 3l7 6 7-6" stroke="#0d0d0e" stroke-width="1.3" fill="none"/></svg>elena@moravel.co.nz</li>
        <li><svg viewBox="0 0 16 16" aria-hidden="true"><circle cx="8" cy="8" r="6.5" stroke="#5ab8ec" stroke-width="1.4" fill="none"/><path d="M1.5 8h13M8 1.5c-3 3.5-3 9.5 0 13M8 1.5c3 3.5 3 9.5 0 13" stroke="#5ab8ec" stroke-width="1.1" fill="none"/></svg>www.moravel.co.nz</li>
      </ul>
    </div>
    <div class="social" aria-hidden="true">
      <span class="social-dot"></span>
      <span class="social-dot"></span>
    </div>
  </section>

  <section class="card card-back" aria-label="Card back">
    <div class="brand">
      <span class="brand-mark"></span>
      <span class="brand-name">Moravel<br>Aesthetic Doctor</span>
    </div>
    <div class="divider"></div>
    <p class="services">
      Dermal injectables<span class="sep"></span>Plasma facials<span class="sep"></span>Microneedling<br>
      Skin boosters<span class="sep"></span>Excessive sweating<br>
      Home and Spa Based Treatments
    </p>
  </section>
</main>
</body>
</html>
```